Trabworth Business Cards

We need a business card design for Trabworth Mining.

This is a B2B company that buys and sells large machinery tires within the coal mining industry. The design should the strong, crisp and masculine. I have uploaded the company logo and rough mock-up of what the back of the card should look like. the front of the card should have the same look/feel as the back. I need editable templates for both the front and the back of the card.

Color scheme should be grey/green/black

Contact information to include on the card:
Name: Dale Pembrose
Title: Managing Director
Phone: 555-314-2069
Address: 1187 Welford #3 Dallas, TX 75290
Email: Dale@Trabworth-example.com

I am also opening a contest for letterhead design. If you submit a business card design, please also submit a letterhead design with the same look/feel. The winner of the business card design will also will the letter head and be paid for both.

Target Market(s)

Procurement men/women in the coal mining industry

Industry/Entity Type

Coal Mining

```html
<!DOCTYPE html>
<html lang="en">
<head>
<meta charset="utf-8">
<title>Trabworth Mining — Business Card</title>
<link rel="stylesheet" href="https://fonts.googleapis.com/css2?family=Mulish:wght@400;600;800&display=swap">
<style>
  :root {
    --backdrop: #3a3b3d;
    --card-light: #e6e6e5;
    --card-dark: #4a4b4d;
    --ink: #47484a;
    --ink-soft: #5c5d5f;
    --green: #5c9e2e;
    --white: #f2f2f0;
  }
  * { box-sizing: border-box; margin: 0; padding: 0; }
  html, body {
    width: 1200px; height: 900px; overflow: hidden;
    background: var(--backdrop);
    font-family: "Mulish", sans-serif;
  }
  .canvas {
    width: 1200px; height: 900px;
    display: flex; flex-direction: column;
    align-items: center; justify-content: center; gap: 60px;
  }
  .card {
    position: relative;
    width: 630px; height: 360px;
    overflow: hidden;
    box-shadow: 0 10px 24px rgba(0,0,0,.35);
  }

  /* Front */
  .card--front { background: var(--card-light); color: var(--ink); }
  .wordmark {
    position: absolute; right: 46px; top: 70px;
    text-align: right; display: flex; align-items: center; gap: 12px;
  }
  .wordmark__square { width: 14px; height: 14px; background: var(--green); }
  .wordmark__name {
    font-weight: 800; font-size: 38px; letter-spacing: 1px; line-height: 1;
    color: var(--ink);
  }
  .wordmark__sub {
    position: absolute; right: 46px; top: 114px;
    font-weight: 800; font-size: 12px; letter-spacing: 24px; margin-right: -24px;
    color: var(--green);
  }
  .person { position: absolute; left: 44px; top: 150px; }
  .person__name { font-weight: 800; font-size: 17px; letter-spacing: .5px; }
  .person__title { font-size: 13px; margin-top: 4px; color: var(--ink-soft); }
  .contact {
    position: absolute; left: 250px; top: 235px;
    font-size: 13.5px; color: var(--ink-soft);
  }
  .contact__row { display: flex; align-items: center; gap: 8px; height: 22px; }
  .contact__row svg { width: 14px; height: 14px; flex: none; }
  .address {
    position: absolute; right: 46px; top: 258px;
    font-size: 13.5px; line-height: 20px; color: var(--ink-soft);
  }
  .edge-band { position: absolute; left: 0; bottom: 0; width: 630px; height: 26px; }

  /* Back */
  .card--back {
    background: var(--card-dark);
    display: flex; flex-direction: column; align-items: center; justify-content: center;
  }
  .card--back .wordmark__name { color: var(--white); font-size: 46px; }
  .back-sub {
    margin-top: 8px; margin-right: -28px;
    font-weight: 800; font-size: 14px; letter-spacing: 28px; color: var(--green);
  }
</style>
</head>
<body>
<main class="canvas">

  <section class="card card--front" aria-label="Card front">
    <div class="wordmark">
      <span class="wordmark__square"></span>
      <span class="wordmark__name">TRABWORTH</span>
    </div>
    <div class="wordmark__sub">MINING</div>

    <div class="person">
      <p class="person__name">DALE PEMBROSE</p>
      <p class="person__title">Managing Director</p>
    </div>

    <div class="contact">
      <div class="contact__row">
        <svg viewBox="0 0 16 16" aria-hidden="true">
          <circle cx="8" cy="8" r="7" fill="none" stroke="var(--green)" stroke-width="1.4"/>
          <path d="M5.5 4.5l1.4 1.6-.8 1c.5 1 1.2 1.7 2.2 2.2l1-.8 1.6 1.4-.9 1.3C7.6 11 5 8.4 4.7 5.6z" fill="var(--green)"/>
        </svg>
        <span>555-314-2069</span>
      </div>
      <div class="contact__row">
        <svg viewBox="0 0 16 16" aria-hidden="true">
          <circle cx="8" cy="8" r="7" fill="none" stroke="var(--green)" stroke-width="1.4"/>
          <rect x="4.3" y="5.3" width="7.4" height="5.4" fill="none" stroke="var(--green)" stroke-width="1.1"/>
          <path d="M4.3 5.3L8 8.3l3.7-3" fill="none" stroke="var(--green)" stroke-width="1.1"/>
        </svg>
        <span>Dale@Trabworth-example.com</span>
      </div>
    </div>

    <div class="address">
      <p>1187 Welford #3</p>
      <p>Dallas, TX 75290</p>
    </div>

    <svg class="edge-band" viewBox="0 0 630 26" aria-hidden="true">
      <polygon points="0,0 250,0 272,26 0,26" fill="var(--green)"/>
      <polygon points="262,10 630,10 630,26 276,26" fill="var(--card-dark)"/>
    </svg>
  </section>

  <section class="card card--back" aria-label="Card back">
    <span class="wordmark__name">TRABWORTH</span>
    <span class="back-sub">MINING</span>
  </section>

</main>
</body>
</html>
```